packaging Design Project

We would like to receive amazing design for our packaging sanitary napkin brand VELORA to catch customers
1)we have attached a file named TRANQUIS design but it is just a reference for taking the information please avoid to do a similar design as the brands are differents .As reference for the map of the design some modifications should be done on the sizes as per the following:
instead 12mm/24mm/90mm/24mm/12mm
it should be 25mm/35mm/120mm/35mm/25mm
instead 83mm/48mm/83mm/48mm/
it should be 105mm/65mm/105mm/65mm
2)our contact information have been changed and the new ones are as per the following:
Phone:(509)3-628-4105
:(509)3-840-2391
E-mail:info@harbvalesupply.com
3)we have attached the VELORA sanitary pictures to be redesigned as per Brevlo is done on its packaging.This is a very important point of the the design you will submit.
4)our company logo is attached
5)we need the design in CMYK format as it is for printing with the specified pantone number .
6)you can pick pictures from pictoravault.com if you win we will buy it.
7)Please go to the supermarket or drugstore to have a better idea how the design should be but we are not required a copy of any brand.
8)five water drops in red or pink color should be in the both front to indicate the high absorption quality.
9) 8 pads.serviettes.toallas to indicate the qty per package.
10)a big word (MAXI) should be writted in the both front to indicate its high absorption.
11)275mm to indicate the lenght.
12)write SANITARY NAPKIN below the word VELORA.
13)reduce the size of our company logo and put it in the both front at the top on the left side.
14)please read the brief time to time because we are upgraded information time to time too.
15)Any doubt or question please send me a message.
N.B: the packaging design should be able to compete with BREVLO MAXI or Durna so be creative to develop an amazing and innovative design.
Updates
please redesign the velora sanitary picture with each detail to be attractive,this is one of most importamt part of the design.
Reason: need more designs and some designers have required more time.
now the deadline is for may 13th.
please do not put barcode number.
Reason: need of amazing designs
don't work with the tranquis sanitary picture but with the velora sanitary picture.you should design the velora sanitary picture to refelct all of its details to be amazing.
Reason: lack of good designs
Target Market(s)
woman from 12 to 45 years old
Industry/Entity Type
It Company
Requirements
Must have
- A)the design should have two fronts and the same information in the both front.
B) (MAXI) should be writted in the both front to indicate its high capacity of absorption.
C)five blood drops in red or pink color should be in the both front to indicate the high absorption quality.
D) 8 pads.serviettes.toallas to indicate the qty per package.
E)275mm to indicate the lenght
F)write SANITARY NAPKIN below the word
G)use fresh and innovative colors but feminine colors .
Nice to have
-reduce the size of our company logo and put it in the both front at the top of the left side.
Should not have
- -please don't put flowers because the pad dosen't have any scent or perfume.
-Please do not put barcode number.

```html
<!DOCTYPE html>
<html lang="en">
<head>
<meta charset="utf-8">
<title>Velora Maxi – Pack Front</title>
<link rel="stylesheet" href="https://fonts.googleapis.com/css2?family=Pinyon+Script&family=Tinos:wght@400;700&family=Arimo:wght@400;700&display=swap">
<style>
  :root {
    --cream: #faf3b8;
    --butter: #f3e27a;
    --lime: #b9cf3c;
    --leaf: #9cba32;
    --olive-dark: #3f4d18;
    --olive: #66772a;
    --ink: #2a2718;
    --pad-white: #f4f6fb;
    --pad-shade: #c9d2e6;
  }
  html, body {
    margin: 0;
    padding: 0;
    overflow: hidden;
    background: #ffffff;
  }
  .pack-front {
    position: relative;
    width: 1200px;
    height: 1001px;
    overflow: hidden;
    background: var(--cream);
  }
  .pack-front__art {
    position: absolute;
    inset: 0;
    width: 1200px;
    height: 1001px;
  }
  .brand-name {
    position: absolute;
    left: 160px;
    top: 150px;
    margin: 0;
    font-family: "Pinyon Script", cursive;
    font-weight: 400;
    font-size: 250px;
    line-height: 1;
    color: var(--ink);
  }
  .product-line {
    position: absolute;
    left: 700px;
    top: 400px;
    margin: 0;
    font-family: "Tinos", serif;
    font-weight: 400;
    font-size: 96px;
    line-height: 1;
    letter-spacing: 1px;
    color: var(--ink);
  }
  .pad-length {
    position: absolute;
    left: 244px;
    top: 563px;
    font-family: "Tinos", serif;
    font-weight: 700;
    font-size: 30px;
    color: var(--ink);
  }
  .pad-length__unit {
    font-size: 20px;
    font-weight: 400;
  }
  .pack-info {
    position: absolute;
    left: 440px;
    top: 720px;
    margin: 0;
    font-family: "Arimo", sans-serif;
    font-size: 36px;
    line-height: 1;
    color: var(--ink);
    white-space: nowrap;
  }
  .pack-info__type {
    color: #ffffff;
    margin-right: 18px;
  }
  .pack-info__count {
    font-weight: 700;
    font-size: 40px;
  }
</style>
</head>
<body>
  <main class="pack-front">
    <svg class="pack-front__art" viewBox="0 0 1200 1001" xmlns="http://www.w3.org/2000/svg">
      <defs>
        <linearGradient id="windowTone" x1="0" y1="0" x2="1" y2="0">
          <stop offset="0" stop-color="#a7b43a"/>
          <stop offset="0.35" stop-color="#c9d84a"/>
          <stop offset="0.7" stop-color="#9aa62c"/>
          <stop offset="1" stop-color="#5d6a1e"/>
        </linearGradient>
        <linearGradient id="bandTone" x1="0" y1="0" x2="0" y2="1">
          <stop offset="0" stop-color="#56662a"/>
          <stop offset="1" stop-color="#3a4716"/>
        </linearGradient>
        <linearGradient id="padTone" x1="0" y1="0" x2="1" y2="1">
          <stop offset="0" stop-color="#ffffff"/>
          <stop offset="1" stop-color="#dfe5f2"/>
        </linearGradient>
      </defs>

      <!-- background waves -->
      <rect class="wave wave--cream" x="0" y="0" width="1200" height="1001" fill="var(--cream)"/>
      <path class="wave wave--lime-top" fill="var(--lime)"
            d="M0 150 H1200 V190 C1000 205 860 180 700 215 C520 255 320 250 0 330 Z"/>
      <path class="wave wave--butter" fill="var(--butter)"
            d="M0 330 C320 250 520 255 700 215 C860 180 1000 205 1200 190 V330 C1000 350 820 330 640 395 C430 470 220 470 0 520 Z"/>
      <path class="wave wave--lime-mid" fill="#d6e06a"
            d="M0 600 C180 560 330 610 470 650 C700 715 950 700 1200 690 V760 H0 Z"/>
      <path class="wave wave--leaf-low" fill="var(--leaf)"
            d="M0 700 C250 690 470 730 700 745 C900 758 1060 740 1200 720 V820 H0 Z"/>
      <path class="wave wave--butter-low" fill="var(--butter)"
            d="M0 790 C300 770 700 800 1200 780 V830 H0 Z"/>

      <!-- top and bottom decorative borders -->
      <rect class="border border--top" x="0" y="0" width="1200" height="165"
            fill="url(#bandTone)" role="img" aria-label="Dark olive lace border band"/>
      <rect class="border border--bottom" x="0" y="795" width="1200" height="206"
            fill="url(#bandTone)" role="img" aria-label="Dark olive lace border band"/>

      <!-- product window -->
      <path class="product-window" fill="url(#windowTone)" role="img"
            aria-label="View of stacked sanitary pads inside the pack"
            d="M455 670 C560 560 760 520 980 495 C1080 484 1150 478 1200 472 V668 C1000 690 760 700 455 670 Z"/>

      <!-- pad illustration -->
      <path class="pad-shadow" fill="#9aa83a" opacity="0.7"
            d="M30 600 C70 580 140 590 175 620 C190 660 160 700 110 705 C60 708 25 680 30 600 Z"/>
      <g class="pad-illustration" role="img" aria-label="Winged sanitary napkin illustration">
        <rect x="100" y="475" width="150" height="270" rx="70"
              transform="rotate(-28 175 610)" fill="url(#padTone)" stroke="var(--pad-shade)" stroke-width="3"/>
      </g>

      <!-- length arrow -->
      <g class="length-arrow" fill="none" stroke="var(--ink)" stroke-width="3" stroke-linecap="round">
        <path d="M186 482 C200 580 250 640 350 668"/>
        <path d="M176 500 L186 478 L200 496"/>
        <path d="M330 656 L354 669 L332 680"/>
      </g>

      <!-- absorbency drops -->
      <g class="absorbency-drops" fill="var(--ink)">
        <path d="M995 672 C1003 684 1008 690 1008 697 A9 9 0 0 1 990 697 C990 690 995 684 995 672 Z"/>
        <path d="M1019 672 C1027 684 1032 690 1032 697 A9 9 0 0 1 1014 697 C1014 690 1019 684 1019 672 Z"/>
        <path d="M1043 672 C1051 684 1056 690 1056 697 A9 9 0 0 1 1038 697 C1038 690 1043 684 1043 672 Z"/>
        <path d="M1067 672 C1075 684 1080 690 1080 697 A9 9 0 0 1 1062 697 C1062 690 1067 684 1067 672 Z"/>
        <path d="M1091 672 C1099 684 1104 690 1104 697 A9 9 0 0 1 1086 697 C1086 690 1091 684 1091 672 Z"/>
      </g>
    </svg>

    <h1 class="brand-name">Velora</h1>
    <p class="product-line">MAXI</p>
    <div class="pad-length">275 <span class="pad-length__unit">mm</span></div>
    <p class="pack-info">
      <span class="pack-info__type">sanitary napkin</span>
      <span class="pack-info__count">8</span> pads servittes toallas
    </p>
  </main>
</body>
</html>
```